New business stationairy

I need paper with header and footer and business cards.
I am a Ltd Company and my main field of expertise is QA/QC inspection in the Oil and Gas Industry. I will need all contact detail inserted and a footer with registration number and bank details etc

```html
<!DOCTYPE html>
<html lang="en">
<head>
<meta charset="utf-8">
<title>Harrow Inspection Services Ltd – Letterhead</title>
<link rel="stylesheet" href="https://fonts.googleapis.com/css2?family=Questrial&display=swap">
<style>
  :root {
    --backdrop: #ececec;
    --paper: #f7f7f7;
    --brand-blue: #1f6fc4;
    --band-dark: #2b4c9c;
    --band-light: #1e9ad6;
    --subtitle-grey: #5b6470;
    --band-text: #ffffff;
  }
  * { box-sizing: border-box; margin: 0; padding: 0; }
  html, body {
    width: 1200px;
    height: 936px;
    overflow: hidden;
    background: var(--backdrop);
    font-family: "Questrial", "Century Gothic", sans-serif;
  }
  .canvas {
    position: relative;
    width: 1200px;
    height: 936px;
  }
  .letterhead {
    position: absolute;
    left: 110px;
    top: 40px;
    width: 608px;
    height: 860px;
    background: var(--paper);
    box-shadow: 0 2px 6px rgba(0,0,0,0.12), 0 12px 30px rgba(0,0,0,0.08);
  }
  .letterhead-brand {
    position: absolute;
    left: 60px;
    top: 56px;
    display: flex;
    flex-direction: column;
    align-items: center;
  }
  .brand-dot {
    width: 32px;
    height: 32px;
    border-radius: 50%;
    background: var(--brand-blue);
    margin-bottom: 8px;
  }
  .letterhead-brand .brand-name {
    font-size: 26px;
    letter-spacing: 2px;
    color: var(--brand-blue);
    line-height: 1;
  }
  .letterhead-brand .brand-sub {
    font-size: 9px;
    letter-spacing: 0.6px;
    color: var(--subtitle-grey);
    margin-top: 4px;
  }
  .footer-band {
    position: absolute;
    left: 0;
    bottom: 0;
    width: 100%;
    height: 76px;
    background: linear-gradient(90deg, var(--band-dark), var(--band-light));
    color: var(--band-text);
    display: flex;
    flex-direction: column;
    justify-content: center;
    align-items: flex-end;
    padding-right: 28px;
    font-size: 10.5px;
    line-height: 1.6;
  }
  .footer-band strong { font-weight: 400; text-decoration: none; opacity: 1; }
  .footer-band .label { font-weight: 400; letter-spacing: 0.2px; }
  .brand-lockup {
    position: absolute;
    left: 800px;
    top: 60px;
    width: 340px;
    display: flex;
    flex-direction: column;
    align-items: center;
  }
  .brand-lockup .brand-dot {
    width: 62px;
    height: 62px;
    margin-bottom: 18px;
  }
  .brand-lockup .brand-name {
    font-size: 40px;
    letter-spacing: 3px;
    color: var(--brand-blue);
    line-height: 1;
  }
  .brand-lockup .brand-sub {
    font-size: 13px;
    letter-spacing: 1px;
    color: var(--subtitle-grey);
    margin-top: 8px;
  }
</style>
</head>
<body>
<main class="canvas">
  <section class="letterhead" aria-label="Company letterhead">
    <header class="letterhead-brand">
      <span class="brand-dot" aria-hidden="true"></span>
      <span class="brand-name">HARROW</span>
      <span class="brand-sub">INSPECTION SERVICES LTD</span>
    </header>
    <footer class="footer-band">
      <p>The Willows, Mill Road, Ashcombe, Marden Vale, Kent, TN9 4QR</p>
      <p><span class="label">Phone:</span> +07700 914382 &nbsp;<span class="label">Email:</span> office@harrowinspect.co.uk &nbsp;Company registration No: 8125604</p>
    </footer>
  </section>

  <aside class="brand-lockup" aria-label="Brand name">
    <span class="brand-dot" aria-hidden="true"></span>
    <span class="brand-name">HARROW</span>
    <span class="brand-sub">INSPECTION SERVICES LTD</span>
  </aside>
</main>
</body>
</html>
```